Label for kQm Ranch beef tallow

I need a small label to go on a 2oz amber glass jar as well as a 4 oz. amber glass jar of moisturizer.
I prefer it to be rectangular for the 2oz jar since it's small and square for the 4oz jar.
I'd like to keep our kQm Ranch logo the same font and style, which is attached. Ten Sleep, Wyoming should be left out. The font for kQm Ranch is spartan.
The label content is as follows:
Signature Tallow
Whipped Moisturizer
Ingredients: Beef Tallow, jojoba oil, peppermint oil.
2oz. jar

Instead of a white label, I'm thinking of a tan or brown label that will blend in with the amber jar. The lettering could then be a white, cream or even rust/burgandy color. Something to give it a rich look.

Thank you!

Target Market(s)

Mainly women but men as well.

Industry/Entity Type

Ranching and online beef sales

Requirements
Must have
• kQm Ranch logo

```html
<!DOCTYPE html>
<html lang="en">
<head>
<meta charset="utf-8">
<title>kQm Ranch — Signature Tallow Labels</title>
<link href="https://fonts.googleapis.com/css2?family=League+Spartan:wght@400&family=Montserrat:wght@600;700&family=Great+Vibes&display=swap" rel="stylesheet">
<style>
  :root {
    --canvas: #e6e6e6;
    --label: #000000;
    --ink: #ffffff;
    --band: #ffffff;
    --band-ink: #111111;
  }
  * { margin: 0; padding: 0; box-sizing: border-box; }
  html, body {
    width: 1200px;
    height: 1200px;
    overflow: hidden;
    background: var(--canvas);
  }
  .sheet {
    position: relative;
    width: 1200px;
    height: 1200px;
  }
  .label {
    position: absolute;
    background: var(--label);
    color: var(--ink);
    overflow: hidden;
  }
  .label--jar-2oz {
    left: 139px;
    top: 484px;
    width: 431px;
    height: 233px;
    border-radius: 32px;
  }
  .label--jar-4oz {
    left: 628px;
    top: 385px;
    width: 430px;
    height: 431px;
    border-radius: 30px;
  }
  .line {
    position: absolute;
    left: 0;
    width: 100%;
    text-align: center;
    line-height: 1;
    white-space: nowrap;
  }
  .brand-mark, .brand-word {
    font-family: "League Spartan", sans-serif;
    font-weight: 400;
    color: var(--ink);
  }
  .product-name {
    font-family: "Montserrat", sans-serif;
    font-weight: 600;
  }
  .ingredients, .net-weight {
    font-family: "Montserrat", sans-serif;
    font-weight: 700;
  }
  .signature-band {
    position: absolute;
    background: var(--band);
    display: flex;
    align-items: center;
    justify-content: center;
  }
  .signature-text {
    font-family: "Great Vibes", cursive;
    color: var(--band-ink);
    white-space: nowrap;
    line-height: 1;
  }

  /* 2oz rectangular label */
  .label--jar-2oz .signature-band {
    left: 61px;
    top: 0;
    width: 26px;
    height: 100%;
  }
  .label--jar-2oz .signature-text {
    font-size: 22px;
    transform: rotate(-90deg);
  }
  .label--jar-2oz .content {
    position: absolute;
    left: 110px;
    right: 10px;
    top: 0;
    bottom: 0;
  }
  .label--jar-2oz .brand-mark { top: 34px; font-size: 64px; }
  .label--jar-2oz .brand-word { top: 119px; font-size: 27px; }
  .label--jar-2oz .product-name { top: 163px; font-size: 17px; }
  .label--jar-2oz .ingredients { top: 188px; font-size: 10px; }
  .label--jar-2oz .net-weight { top: 212px; font-size: 10px; }

  /* 4oz square label */
  .label--jar-4oz .signature-band {
    left: 0;
    top: 58px;
    width: 100%;
    height: 33px;
  }
  .label--jar-4oz .signature-text { font-size: 26px; }
  .label--jar-4oz .brand-mark { top: 132px; font-size: 112px; }
  .label--jar-4oz .brand-word { top: 258px; font-size: 42px; }
  .label--jar-4oz .product-name { top: 326px; font-size: 26px; }
  .label--jar-4oz .ingredients { top: 362px; font-size: 15px; }
  .label--jar-4oz .net-weight { top: 401px; font-size: 13px; }
</style>
</head>
<body>
  <main class="sheet">
    <section class="label label--jar-2oz" aria-label="2oz jar label">
      <div class="signature-band"><span class="signature-text">Signature Tallow</span></div>
      <div class="content">
        <div class="line brand-mark">kQm</div>
        <div class="line brand-word">RANCH</div>
        <div class="line product-name">WHIPPED MOISTURIZER</div>
        <div class="line ingredients">Beef Tallow, jojoba oil, peppermint oil</div>
        <div class="line net-weight">2oz.</div>
      </div>
    </section>

    <section class="label label--jar-4oz" aria-label="4oz jar label">
      <div class="signature-band"><span class="signature-text">Signature Tallow</span></div>
      <div class="line brand-mark">kQm</div>
      <div class="line brand-word">RANCH</div>
      <div class="line product-name">WHIPPED MOISTURIZER</div>
      <div class="line ingredients">Beef Tallow, jojoba oil, peppermint oil</div>
      <div class="line net-weight">4oz.</div>
    </section>
  </main>
</body>
</html>
```